Hvac and insulation company needs good looking business card design

We are hvac and insulation company and looking for a new business cards that look to today standards designs

Target Market(s)

homeowners

Industry/Entity Type

Hvac

Contact Information for Business Card

Name: Walter Brinoku
Home comfort consultant
address: 4827 Dunmore St #215 Oakland, CA 94619
office: 888-316-2790
cell: 510-742-3185
Lic.# 584261
Email: walter@corvane-hvac.com
Web: corvane-hvac.com

Requirements
Must have
• clean and sleek look
Nice to have
• simple with a clean look
Should not have
• to busy business card

```html
<!DOCTYPE html>
<html lang="en">
<head>
<meta charset="UTF-8">
<title>Corvane Business Card</title>
<link rel="stylesheet" href="https://fonts.googleapis.com/css2?family=Arimo:wght@400;700&display=swap">
<style>
  :root {
    --stage-bg: #222222;
    --card-white: #ffffff;
    --brand-orange: #f5821f;
    --ink: #1f1f1f;
    --rule-grey: #8a8a8a;
    --card-shadow: rgba(0, 0, 0, 0.55);
  }
  * { box-sizing: border-box; margin: 0; padding: 0; }
  html, body {
    width: 1200px;
    height: 900px;
    overflow: hidden;
    background: var(--stage-bg);
    font-family: "Arimo", Arial, sans-serif;
  }
  .stage { position: relative; width: 1200px; height: 900px; }
  .card {
    position: absolute;
    top: 306px;
    width: 440px;
    height: 271px;
    border-radius: 11px;
    box-shadow: 2px 4px 6px var(--card-shadow);
    overflow: hidden;
  }
  .card-front { left: 149px; background: var(--card-white); color: var(--ink); }
  .card-back { left: 608px; background: var(--brand-orange); }

  .brand {
    position: absolute;
    top: 50px;
    right: 24px;
    display: flex;
    align-items: center;
    gap: 12px;
  }
  .brand-dot {
    width: 30px; height: 30px;
    border-radius: 50%;
    background: var(--brand-orange);
  }
  .brand-name {
    font-size: 44px;
    font-weight: 700;
    color: var(--brand-orange);
    line-height: 1;
    letter-spacing: -0.5px;
  }

  .holder-name {
    position: absolute; left: 21px; top: 152px;
    font-size: 19px; font-weight: 700; color: var(--brand-orange);
  }
  .holder-title {
    position: absolute; left: 21px; top: 175px;
    font-size: 12.5px;
  }
  .title-rule {
    position: absolute; left: 179px; top: 183px;
    width: 236px; height: 1px; background: var(--rule-grey);
  }
  .license {
    position: absolute; right: 25px; top: 154px;
    font-size: 13px;
  }
  .license-label { color: var(--brand-orange); }

  .address {
    position: absolute; left: 21px; top: 216px;
    font-size: 13px; line-height: 16px; font-style: normal;
  }
  .contact-list {
    position: absolute; right: 24px; top: 202px;
    list-style: none;
    font-size: 13px; line-height: 16px;
    text-align: right;
  }
  .contact-list li { display: flex; justify-content: flex-end; align-items: center; gap: 2px; }
  .contact-icon { width: 10px; height: 10px; fill: var(--brand-orange); }

  .back-pattern { position: absolute; inset: 0; background: var(--brand-orange); }
  .back-brand {
    position: absolute; left: 0; right: 0; top: 128px;
    text-align: center;
    font-size: 40px; font-weight: 700; color: var(--card-white);
    line-height: 1;
  }
  .back-web {
    position: absolute; left: 0; right: 0; top: 232px;
    text-align: center; font-size: 13px; color: var(--card-white);
  }
</style>
</head>
<body>
<main class="stage">
  <section class="card card-front">
    <div class="brand">
      <span class="brand-dot"></span>
      <span class="brand-name">corvane</span>
    </div>

    <h1 class="holder-name">Walter Brinoku</h1>
    <p class="holder-title">Home Comfort Consultant</p>
    <span class="title-rule"></span>
    <p class="license"><span class="license-label">LIC.</span># 584261</p>

    <address class="address">4827 Dunmore St<br>#215 Oakland, CA 94619</address>

    <ul class="contact-list">
      <li>888-316-2790
        <svg class="contact-icon" viewBox="0 0 10 10" aria-hidden="true"><path d="M1 3.5C1 2 2.5 1.2 5 1.2S9 2 9 3.5L7.3 4.2 6.8 3.2H3.2L2.7 4.2Z"/><path d="M2.5 5h5l1 3.8h-7z"/></svg>
      </li>
      <li>510-742-3185
        <svg class="contact-icon" viewBox="0 0 10 10" aria-hidden="true"><path d="M3 0.5h4a1 1 0 0 1 1 1v7a1 1 0 0 1-1 1H3a1 1 0 0 1-1-1v-7a1 1 0 0 1 1-1zm0.3 1.2v5.8h3.4V1.7z"/></svg>
      </li>
      <li>walter@corvane-hvac.com
        <svg class="contact-icon" viewBox="0 0 10 10" aria-hidden="true"><path d="M0.5 2h9v6h-9z M0.5 2L5 5.5 9.5 2" stroke="#fff" stroke-width="0.8"/></svg>
      </li>
    </ul>
  </section>

  <section class="card card-back">
    <div class="back-pattern" role="img" aria-label="Faint repeated brand mark pattern on orange"></div>
    <p class="back-brand">corvane</p>
    <p class="back-web">www.corvane-hvac.com</p>
  </section>
</main>
</body>
</html>
```